Osgood Business Card Design

Photography business needs a logo. I would like to see creative licence on options on 1 & 2 sided. I really like the concept of a fully / partially frosted design. I have already used ArtSwarm for my Logo, so I am looking for the same level of assistance with this project.

Industry/Entity Type

Business

Font styles to use
Serif
Script

Requirements
Must have
• Must Have:
• - These are my contact details
• Name: Pim L Osgood
• Mobile: 5813409271
• email: marlaweskin@fernpost.example

```html
<!DOCTYPE html>
<html lang="en">
<head>
<meta charset="utf-8">
<title>Osgood Business Card</title>
<link rel="stylesheet" href="https://fonts.googleapis.com/css2?family=Open+Sans:wght@400;700&display=swap">
<style>
  :root {
    --page-bg: #2a2a2c;
    --card-dark: #2c2728;
    --card-dark-edge: #1f1b1c;
    --card-light: #f3f3f3;
    --ink-dark: #3a3637;
    --ink-white: #ffffff;
    --accent-blue: #3d8fd1;
    --lens-mint: #d8efdd;
    --band-dark: #2f2a2b;
  }
  * { margin: 0; padding: 0; box-sizing: border-box; }
  html, body {
    width: 1200px; height: 800px; overflow: hidden;
    background: var(--page-bg);
    font-family: "Open Sans", Arial, sans-serif;
  }
  .stage {
    position: relative; width: 1200px; height: 800px;
    display: flex; align-items: center; justify-content: center; gap: 60px;
  }
  .card {
    position: relative; width: 520px; height: 298px; overflow: hidden;
    box-shadow: 0 12px 30px rgba(0,0,0,0.45);
  }
  .card--front {
    background: linear-gradient(135deg, var(--card-dark) 0%, var(--card-dark-edge) 100%);
    display: flex; align-items: center; justify-content: center;
  }
  .brand { display: flex; align-items: center; gap: 16px; }
  .brand__dot {
    width: 56px; height: 56px; border-radius: 50%;
    background: var(--lens-mint);
  }
  .brand__name {
    font-weight: 700; font-size: 52px; letter-spacing: 1px;
    color: var(--ink-white);
  }
  .card--back { background: var(--card-light); }
  .band { position: absolute; width: 16px; background: var(--band-dark); }
  .band--right { right: 0; top: 0; height: 118px; }
  .band--left { left: 0; bottom: 0; height: 104px; }
  .details { position: absolute; left: 232px; top: 48px; }
  .brand--small { gap: 10px; margin-bottom: 22px; }
  .brand--small .brand__dot {
    width: 30px; height: 30px; background: var(--lens-mint);
    border: 5px solid var(--ink-dark);
  }
  .brand--small .brand__name { font-size: 28px; color: var(--ink-dark); letter-spacing: 0.5px; }
  .person__name { font-weight: 700; font-size: 17px; color: var(--ink-dark); line-height: 1.2; }
  .person__role { font-size: 13px; color: var(--accent-blue); margin-bottom: 16px; }
  .contact { list-style: none; }
  .contact__item {
    display: flex; align-items: center; gap: 14px;
    font-size: 13px; color: var(--accent-blue); margin-bottom: 12px;
  }
  .contact__icon { width: 16px; height: 16px; flex: none; }
</style>
</head>
<body>
<main class="stage">
  <section class="card card--front" aria-label="Card front">
    <div class="brand">
      <span class="brand__dot"></span>
      <span class="brand__name">Osgood</span>
    </div>
  </section>

  <section class="card card--back" aria-label="Card back">
    <span class="band band--right"></span>
    <span class="band band--left"></span>
    <div class="details">
      <div class="brand brand--small">
        <span class="brand__dot"></span>
        <span class="brand__name">Osgood</span>
      </div>
      <p class="person__name">Pim L Osgood</p>
      <p class="person__role">Photo Manager</p>
      <ul class="contact">
        <li class="contact__item">
          <svg class="contact__icon" viewBox="0 0 16 16" aria-hidden="true">
            <rect x="4" y="1" width="8" height="14" rx="1.5" fill="none" stroke="#3a3637" stroke-width="1.4"/>
            <line x1="7" y1="12.5" x2="9" y2="12.5" stroke="#3a3637" stroke-width="1.2"/>
          </svg>
          <span>Mobile: 5813409271</span>
        </li>
        <li class="contact__item">
          <svg class="contact__icon" viewBox="0 0 16 16" aria-hidden="true">
            <rect x="1" y="3" width="14" height="10" fill="#3a3637"/>
            <polyline points="1,3 8,9 15,3" fill="none" stroke="#f3f3f3" stroke-width="1.2"/>
          </svg>
          <span>Email: marlaweskin@fernpost.example</span>
        </li>
      </ul>
    </div>
  </section>
</main>
</body>
</html>
```